RW Holloway LLC Business Card - Civil Engineering & Consulting Firm

We need a Business Card that is elegant, and masculine.  It is our Professional Civil Engineering & Consulting Company located in San Antonio TX (Not s construction or builder firm- no gears & no tool images please). We provide civil engineering services including  commercial site plans, grading and drainage plans, utility plans, hydraulics and hydrology, land planning, utility coordination, and other general civil engineering services related to commercial and residential development.
We have 2 existing Logos. We would like to convey reliability, strength, trustworthiness and attention to detail.  Blues and orange tones as per logo We are OK with the use of a darker blue in the mix.  We have 2 logo versions - Full Company Name Logo to go on the back of card, & Small Icon Logo for the front w/ personal Info.

Target Market(s)
Architects, Real Estate Developers, Other Strctural Engineers, Surveyers, General Contractors
Industry/Entity Type
Professional Civil Engineering
Contact Information for Business Card
Name, Position, Address, Cell & Office #, email, and company website
Font styles to use
Other font styles liked:
- Avian
Requirements
Should not have
- No Tools, No Gears, no Cranes, or Construction Equipment.

```html
<!DOCTYPE html>
<html lang="en">
<head>
<meta charset="utf-8">
<title>RW Holloway LLC – Business Card</title>
<link rel="stylesheet" href="https://fonts.googleapis.com/css2?family=Josefin+Sans:wght@300&family=Montserrat:wght@400;700&display=swap">
<style>
  :root {
    --backdrop: #1e1e1f;
    --sky: #79a9d4;
    --slate: #a3a3a8;
    --amber: #e6953f;
    --stripe-orange: #ec9129;
    --stripe-blue: #7baed9;
    --paper: #ffffff;
    --paper-shade: #f1f1f1;
    --ink-light: #ffffff;
  }
  * { margin: 0; padding: 0; box-sizing: border-box; }
  html, body { width: 1200px; height: 900px; overflow: hidden; background: var(--backdrop); }
  .canvas { position: relative; width: 1200px; height: 900px; }

  .card {
    position: absolute;
    left: 280px;
    width: 640px;
    height: 366px;
    overflow: hidden;
    box-shadow: 0 10px 30px rgba(0,0,0,.55);
  }
  .card--front { top: 64px; background: linear-gradient(180deg, var(--sky) 0%, var(--slate) 50%, var(--amber) 100%); }
  .card--back { top: 470px; background: linear-gradient(160deg, var(--paper) 40%, var(--paper-shade) 100%); }

  .front-name {
    position: absolute; inset: 0;
    display: flex; align-items: center; justify-content: center;
    font-family: "Josefin Sans", sans-serif;
    font-weight: 300;
    font-size: 50px;
    letter-spacing: 4px;
    color: var(--ink-light);
    text-transform: uppercase;
  }

  .wave { position: absolute; inset: 0; width: 640px; height: 366px; }

  .contact {
    position: absolute; left: 30px; top: 150px;
    font-family: "Montserrat", sans-serif;
    color: var(--ink-light);
  }
  .contact__name { font-weight: 700; font-size: 16px; letter-spacing: 1px; text-transform: uppercase; line-height: 1.2; }
  .contact__role { font-size: 14px; margin-top: 3px; }
  .contact__address { font-size: 13px; line-height: 1.35; margin-top: 10px; }
  .contact__list { list-style: none; margin-top: 8px; font-size: 13px; }
  .contact__list li { display: flex; align-items: center; gap: 9px; height: 21px; }
  .contact__list svg { width: 14px; height: 14px; flex: none; }

  .back-name {
    position: absolute; right: 44px; top: 132px;
    font-family: "Montserrat", sans-serif;
    font-weight: 700;
    font-size: 22px;
    color: var(--stripe-orange);
  }
</style>
</head>
<body>
<main class="canvas">
  <section class="card card--front">
    <h1 class="front-name">RW Holloway LLC</h1>
  </section>

  <section class="card card--back">
    <svg class="wave" viewBox="0 0 640 366" aria-hidden="true">
      <defs>
        <linearGradient id="band" x1="0" y1="0" x2="0" y2="1">
          <stop offset="0" stop-color="#79a9d4"/>
          <stop offset="0.5" stop-color="#a9a7a6"/>
          <stop offset="1" stop-color="#e6953f"/>
        </linearGradient>
      </defs>
      <path d="M0,40 C300,40 300,262 640,262 L640,366 L0,366 Z" fill="#ec9129"/>
      <path d="M0,48 C300,48 300,276 640,276 L640,366 L0,366 Z" fill="#ffffff"/>
      <path d="M0,54 C300,54 300,284 640,284 L640,366 L0,366 Z" fill="#7baed9"/>
      <path d="M0,76 C300,76 300,306 640,306 L640,366 L0,366 Z" fill="#ffffff"/>
      <path d="M0,82 C300,82 300,314 640,314 L640,366 L0,366 Z" fill="url(#band)"/>
    </svg>

    <div class="contact">
      <p class="contact__name">Daniel Whitaker</p>
      <p class="contact__role">Co-Founder</p>
      <p class="contact__address">4180 Alamo Ridge Drive<br>Suite 210 San Antonio</p>
      <ul class="contact__list">
        <li>
          <svg viewBox="0 0 24 24"><path d="M6.6 10.8a15 15 0 0 0 6.6 6.6l2.2-2.2a1 1 0 0 1 1-.25 11.4 11.4 0 0 0 3.6.57 1 1 0 0 1 1 1V20a1 1 0 0 1-1 1A17 17 0 0 1 3 4a1 1 0 0 1 1-1h3.5a1 1 0 0 1 1 1c0 1.250.2 2.450.57 3.570a1 1 0 0 1-.25 1z" fill="#fff"/></svg>
          210-555-0142
        </li>
        <li>
          <svg viewBox="0 0 24 24"><rect x="4" y="9" width="16" height="12" rx="2" fill="#fff"/><path d="M2 8c0-3 20-3 20 0v2h-5V8H7v2H2z" fill="#fff"/></svg>
          210-555-0187
        </li>
        <li>
          <svg viewBox="0 0 24 24"><rect x="2" y="5" width="20" height="14" fill="#fff"/><path d="M2 5l10 8 10-8" fill="none" stroke="#b8a690" stroke-width="1.5"/></svg>
          info@rwhollowayllc
        </li>
        <li>
          <svg viewBox="0 0 24 24"><circle cx="12" cy="12" r="10" fill="#fff"/><path d="M2 12h20M12 2c3 3 3 17 0 20M12 2c-3 3-3 17 0 20" fill="none" stroke="#c9a27a" stroke-width="1.3"/></svg>
          www.rwhollowayllc.com
        </li>
      </ul>
    </div>

    <p class="back-name">RW Holloway LLC</p>
  </section>
</main>
</body>
</html>
```